BOLD & MINIMALIST DESIGN NEEDED

We want a very bold but minimalistic business card design that is impactful and utilizes both sides of the business card. Our current logo is included for your use.

We want bold fonts and good use of negative space. We don't want the logo to overpower the design.

Target Market(s)

Professionals who are building new commercial buildings.

Industry/Entity Type

Construction

Contact Information for Business Card

Name, Title, email, office phone, cell phone, website

Font styles to use
Serif
Sans Serif

Requirements
Must have
• Bold design!

```html
<!DOCTYPE html>
<html lang="en">
<head>
<meta charset="UTF-8">
<title>Ridgeline – Business Card</title>
<link href="https://fonts.googleapis.com/css2?family=PT+Sans:wght@700&family=Poppins:wght@300;400&display=swap" rel="stylesheet">
<style>
  :root {
    --backdrop: #acacac;
    --card-white: #ffffff;
    --card-black: #0a0b0d;
    --ink: #111214;
    --green: #84c225;
    --green-light: #b5dc7a;
    --rule: #c9c9c9;
  }
  * { margin: 0; padding: 0; box-sizing: border-box; }
  html, body {
    width: 1093px; height: 1200px; overflow: hidden;
    background: var(--backdrop);
  }
  .card {
    position: absolute;
    left: 264px;
    width: 580px; height: 357px;
    border-radius: 24px;
    overflow: hidden;
  }
  .card--front { top: 226px; background: var(--card-white); }
  .card--back { top: 621px; background: var(--card-black); }

  .wordmark {
    position: absolute;
    display: flex; align-items: center; gap: 10px;
    font-family: "PT Sans", sans-serif;
    font-weight: 700;
    letter-spacing: 0.5px;
    white-space: nowrap;
  }
  .wordmark__square { display: block; background: var(--green); }
  .card--front .wordmark {
    left: 148px; top: 200px; transform: translateX(-50%);
    font-size: 40px; color: var(--ink);
  }
  .card--front .wordmark__square { width: 22px; height: 22px; }
  .card--back .wordmark {
    left: 50%; top: 50%; transform: translate(-50%, -50%);
    font-size: 56px; color: #f3f3f1;
  }
  .card--back .wordmark__square { width: 30px; height: 30px; }

  .divider {
    position: absolute; left: 289px; top: 74px;
    width: 1px; height: 209px; background: var(--rule);
  }
  .person {
    position: absolute; left: 312px; top: 99px;
  }
  .person__name {
    font-family: "PT Sans", sans-serif; font-weight: 700;
    font-size: 25px; line-height: 27px; color: var(--ink);
  }
  .person__title {
    font-family: "Poppins", sans-serif; font-weight: 300;
    font-size: 17px; line-height: 20px; color: var(--green);
  }
  .contacts {
    position: absolute; left: 312px; top: 169px;
    list-style: none;
    font-family: "Poppins", sans-serif; font-weight: 300;
    font-size: 17px; color: var(--ink);
    white-space: nowrap;
  }
  .contacts li {
    display: flex; align-items: center; gap: 8px;
    height: 21px;
  }
  .contacts svg { width: 15px; height: 15px; flex: none; }
  .swoosh { position: absolute; left: 0; top: 0; }
</style>
</head>
<body>

<section class="card card--front">
  <div class="wordmark"><span class="wordmark__square"></span>RIDGELINE</div>

  <div class="divider"></div>

  <div class="person">
    <h1 class="person__name">MARCUS HALE</h1>
    <p class="person__title">Managing Director</p>
  </div>

  <ul class="contacts">
    <li>
      <svg viewBox="0 0 16 16"><path d="M3 1.5l2.5 0 1 3.5-1.8 1.2c.8 1.8 2.3 3.3 4.1 4.1l1.2-1.8 3.5 1v2.5c0 .8-.7 1.5-1.5 1.5C6.4 13.5 2.5 9.6 1.5 3c0-.8.7-1.5 1.5-1.5z" fill="none" stroke="var(--green)" stroke-width="1.5"/><path d="M9.5 2.5a4 4 0 0 1 4 4M9.5 5a1.5 1.5 0 0 1 1.5 1.5" fill="none" stroke="var(--green)" stroke-width="1.3"/></svg>
      044-987 210 346
    </li>
    <li>
      <svg viewBox="0 0 16 16"><rect x="3.5" y="1" width="9" height="14" rx="1.5" fill="none" stroke="var(--green)" stroke-width="1.5"/><circle cx="8" cy="12.5" r="0.9" fill="var(--green)"/></svg>
      044-987 210 347
    </li>
    <li>
      <svg viewBox="0 0 16 16"><rect x="0.5" y="3.5" width="15" height="10" fill="var(--green)"/><path d="M0.5 3.5L8 9.5l7.5-6M0.5 13.5l5.5-5M15.5 13.5L10 8.5" fill="none" stroke="#fff" stroke-width="1"/></svg>
      hello@ridgeline.com
    </li>
    <li>
      <svg viewBox="0 0 16 16"><circle cx="8" cy="8" r="7" fill="var(--green)"/><path d="M1 8h14M8 1v14M2.5 4.5h11M2.5 11.5h11" stroke="#fff" stroke-width="0.8" fill="none"/><ellipse cx="8" cy="8" rx="3.2" ry="7" fill="none" stroke="#fff" stroke-width="0.8"/></svg>
      www.ridgelinebuild.com
    </li>
  </ul>

  <svg class="swoosh" width="580" height="357" viewBox="0 0 580 357">
    <defs>
      <linearGradient id="swooshGreen" x1="90" y1="0" x2="360" y2="0" gradientUnits="userSpaceOnUse">
        <stop offset="0" stop-color="var(--green-light)" stop-opacity="0.2"/>
        <stop offset="1" stop-color="var(--green)"/>
      </linearGradient>
    </defs>
    <path d="M90 335 C190 314 290 303 360 305 C450 307 520 322 580 336 L580 345 L566 352 C500 336 420 319 340 317 C260 315 180 322 90 335 Z" fill="url(#swooshGreen)"/>
    <path d="M36 357 C140 334 230 322 310 323 C400 324 470 340 536 357 Z" fill="var(--card-black)"/>
  </svg>
</section>

<section class="card card--back">
  <div class="wordmark"><span class="wordmark__square"></span>RIDGELINE</div>
</section>

</body>
</html>
```